NZ First of it's kind solutions directory and marketplace for busy Mums needs a business card design

We need a business card design for our new nationwide business in NZ (long term plans to go global). We provide solutions to the everyday challenges that busy Mums face by connecting them with quality communities and suppliers of carefully selected, relevant products and services. We sell direct via our online marketplace. The final design should communicate our values of inclusivity, quality and smart solutions. Colours should incorporate our logo colour palette of #477077 and #6ba8b2. Our website is at https://www.brightnestmums.example

Target Market(s)

busy Mums, Age 28 – 50, female, income over $100K, location main centres NZ primarily but NZ wide. Is likely juggling work or career with a young family. Probably had hobbies which have fallen by the wayside.
-Wants to succeed in her chosen career without compromising on family life
-to successfully juggle her career without feeling like she is compromising her children
- Is time poor, something always has to give and it’s generally her health (she’ll stay up late, get stressed)
- probably ex corporate or professional career. Has discretional income

Industry/Entity Type

Business

Contact Information for Business Card

Lena Forbisher, Founder, BrightNestMums.example (Strapline Tap; Gather; Sorted), 47 Kowhai Terrace, Ellerslie, Auckland 1051, New Zealand. Mob: 021 483 517 Ph: +64 (0)9 571 4860

Font styles to use
Other font styles liked:
• Raleway, and/or Architects Daughter

Colors
00a990
33b8a4
86cfc6
cfeae6

Requirements
Must have
• the above details, streamline. the logo and colours associated with those logos
Should not have
• foil or metallic colours

```html
<!DOCTYPE html>
<html lang="en">
<head>
<meta charset="utf-8">
<title>BrightNestMums – Business Card</title>
<link rel="stylesheet" href="https://fonts.googleapis.com/css2?family=Arimo:wght@400;700&display=swap">
<style>
  :root {
    --brand-deep: #477077;
    --brand-light: #6ba8b2;
    --ink: #222628;
    --card-front: #ffffff;
    --card-back: #f7f7f7;
    --backdrop: #e6e8e8;
  }
  * { box-sizing: border-box; margin: 0; padding: 0; }
  html, body {
    width: 1200px; height: 900px; overflow: hidden;
    background: var(--backdrop);
    font-family: "Arimo", Arial, sans-serif;
    color: var(--ink);
  }
  .canvas { position: relative; width: 1200px; height: 900px; }
  .card {
    position: absolute;
    box-shadow: 0 2px 8px rgba(0,0,0,0.12);
  }
  .card--front { left: 177px; top: 73px; width: 589px; height: 365px; background: var(--card-front); }
  .card--back { left: 388px; top: 482px; width: 567px; height: 352px; background: var(--card-back); }

  .brand-disc {
    position: absolute; left: 14px; top: 102px;
    width: 190px; height: 190px; border-radius: 50%;
    background: var(--brand-deep);
  }
  .identity { position: absolute; right: 36px; top: 52px; text-align: right; }
  .identity__name { font-size: 22px; font-weight: 700; letter-spacing: 0.5px; line-height: 1.1; }
  .identity__first { color: var(--brand-deep); }
  .identity__last { color: var(--brand-light); }
  .identity__role { font-size: 16px; margin-top: 5px; }

  .contact { position: absolute; right: 36px; top: 189px; text-align: right; font-size: 16px; line-height: 22px; }
  .contact__line { display: flex; justify-content: flex-end; align-items: center; gap: 4px; }
  .contact__icon { width: 13px; height: 13px; fill: var(--brand-light); }
  .address { margin-top: 8px; margin-right: 0; }

  .wordmark {
    position: absolute; left: 0; right: 0; top: 146px;
    display: flex; justify-content: center; align-items: center; gap: 12px;
  }
  .wordmark__dot { width: 30px; height: 30px; border-radius: 50%; background: var(--brand-deep); }
  .wordmark__name { font-size: 34px; font-weight: 700; color: var(--brand-deep); letter-spacing: -0.5px; }
  .web { position: absolute; left: 0; right: 0; top: 281px; text-align: center; font-size: 15px; font-weight: 700; color: var(--brand-deep); }
</style>
</head>
<body>
<main class="canvas">
  <section class="card card--front" aria-label="Business card front">
    <div class="brand-disc" aria-hidden="true"></div>
    <div class="identity">
      <p class="identity__name"><span class="identity__first">LENA</span> <span class="identity__last">FORBISHER</span></p>
      <p class="identity__role">Founder</p>
    </div>
    <div class="contact">
      <p class="contact__line">021 483 517
        <svg class="contact__icon" viewBox="0 0 16 16" aria-hidden="true"><path d="M2 6c0-2 2-3 6-3s6 1 6 3v1h-3V5.5C10 5 9 5 8 5s-2 0-3 .5V7H2zm2 2h8l1.5 5h-11z"/></svg></p>
      <p class="contact__line">+64 (0)9 571 4860
        <svg class="contact__icon" viewBox="0 0 16 16" aria-hidden="true"><path d="M4 1h8v14H4zm1.5 1.5v9h5v-9z"/></svg></p>
      <p class="contact__line">www.BrightNestMums.example
        <svg class="contact__icon" viewBox="0 0 16 16" aria-hidden="true"><circle cx="8" cy="8" r="7"/><path d="M5 4c2 1 1 3 3 3s1 3 3 3" stroke="#fff" stroke-width="1.3" fill="none"/></svg></p>
      <p class="address">47 Kowhai Terrace, Ellerslie<br>Auckland 1051, New Zealand</p>
    </div>
  </section>

  <section class="card card--back" aria-label="Business card back">
    <div class="wordmark">
      <span class="wordmark__dot" aria-hidden="true"></span>
      <span class="wordmark__name">BrightNestMums</span>
    </div>
    <p class="web">www.BrightNestMums.example</p>
  </section>
</main>
</body>
</html>
```